Personal Motivational Quote Poster Design

I would like to create a poster with some of my favorite quotes to hang in my office. I did similar projects in 2012 and 2014. I've uploaded the winning designs so you can get a better idea of what I'm looking for. I will provide feedback on your design within 24 hours of receiving it.

The poster must contain the following quotes:

“What the pupil must learn, if he learns anything at all, is that the world will do most of the work for you, provided you cooperate with it by identifying how it really works and aligning with those realities. If we do not let the world teach us, it teaches us a lesson.” - Harold Quenby

“I tackle every big new problem by asking two questions: Who has dealt with this problem well? And what can we learn from them?” - Walt Prisco

“If we can really understand the problem, the answer will come out of it, because the answer is not separate from the problem.” - Ravindra Selvapathi

“Success is nothing more than a few simple disciplines, practiced every day; while failure is simply a few errors in judgment, repeated every day. It is the accumulative weight of our disciplines and our judgments that leads us to either fortune or failure.” - Ned Falco

“Inaction breeds doubt and fear. Action breeds confidence and courage.” - Rufus Pembrook

“What’s the one thing you can do, such that by doing it, everything else will be easier or unnecessary?” - Lyle Dorsey

Requirements
Must have
• The poster will be 24" high x 36" long and printed on canvas, so the image you create needs to have a resolution of at least 2700 x 3900.
Nice to have
• I don't have an exact vision for how the poster should look, so I am totally open to you using your creativity to develop, arrange and present the content as you'd like.

That said, I would like an image (photo or posterized image) of the person being quoted along with each quote. I do not have specific images that I would like you to use, so you will need to find the images on your own.

The images don't need to be perfect... I am more interested in the poster relating the essence of the quotes and the people being quoted than I am in perfect photographic images of the people being quoted.

```html
<!DOCTYPE html>
<html lang="en">
<head>
<meta charset="utf-8">
<title>Quote Poster</title>
<link rel="stylesheet" href="https://fonts.googleapis.com/css2?family=Dancing+Script:wght@500&display=swap">
<style>
  :root {
    --red: #cf1f31;
    --navy: #2b3f66;
    --coral: #e8504a;
    --cream: #f7edc6;
    --sky: #6b8fe6;
    --lilac: #8d90ea;
    --quote-red: #d62a36;
  }
  html, body {
    margin: 0;
    padding: 0;
    overflow: hidden;
    background: var(--red);
  }
  .poster {
    position: relative;
    width: 831px;
    height: 1200px;
    overflow: hidden;
    background: var(--red);
    font-family: "Dancing Script", cursive;
  }
  .field {
    position: absolute;
    left: 47px;
    top: 0;
    width: 750px;
    height: 1200px;
    background: var(--navy);
  }
  .bands {
    position: absolute;
    left: 0;
    top: 0;
    width: 831px;
    height: 1200px;
  }
  .portrait {
    position: absolute;
    border-radius: 46% 46% 30% 30% / 40% 40% 22% 22%;
  }
  .portrait--dorsey { left: 83px; top: 52px; width: 157px; height: 164px;
    background: radial-gradient(ellipse at 50% 40%, #e8504a 0%, #e8504a 40%, #4c6fd4 75%, #2b3f66 100%); }
  .portrait--selvapathi { left: 646px; top: 193px; width: 112px; height: 167px;
    background: radial-gradient(ellipse at 45% 40%, #f7edc6 0%, #e8504a 45%, #2b3f66 90%); }
  .portrait--falco { left: 81px; top: 419px; width: 151px; height: 175px;
    background: radial-gradient(ellipse at 55% 35%, #e8504a 0%, #e8504a 35%, #6b8fe6 65%, #22376a 100%); }
  .portrait--prisco { left: 646px; top: 615px; width: 125px; height: 182px;
    background: radial-gradient(ellipse at 50% 40%, #f7edc6 0%, #e8504a 40%, #6b8fe6 70%, #2b3f66 100%); }
  .portrait--pembrook { left: 78px; top: 779px; width: 136px; height: 190px;
    background: radial-gradient(ellipse at 55% 35%, #f7edc6 0%, #e8504a 40%, #2b3f66 85%); }
  .portrait--quenby { left: 623px; top: 930px; width: 166px; height: 185px;
    background: radial-gradient(ellipse at 45% 40%, #f7edc6 0%, #e8504a 40%, #6b8fe6 65%, #2b3f66 100%); }
  .quote {
    position: absolute;
    margin: 0;
    text-align: center;
    font-weight: 500;
    font-size: 23px;
    line-height: 37px;
    white-space: nowrap;
    transform: translateX(-50%);
  }
  .quote span { display: block; }
  .quote--dorsey { left: 487px; top: 78px; color: var(--coral); }
  .quote--selvapathi { left: 370px; top: 241px; color: var(--cream); }
  .quote--falco { left: 495px; top: 399px; color: var(--sky); }
  .quote--prisco { left: 378px; top: 651px; color: var(--cream); }
  .quote--pembrook { left: 485px; top: 875px; color: var(--quote-red); }
  .quote--quenby { left: 375px; top: 961px; color: var(--lilac); }
</style>
</head>
<body>
<div class="poster">
  <div class="field"></div>
  <svg class="bands" viewBox="0 0 831 1200" aria-hidden="true">
    <defs>
      <filter id="rough" x="-5%" y="-5%" width="110%" height="110%">
        <feTurbulence type="fractalNoise" baseFrequency="0.09" numOctaves="2" seed="3" result="n"/>
        <feDisplacementMap in="SourceGraphic" in2="n" scale="14"/>
      </filter>
    </defs>
    <g fill="#cf1f31" filter="url(#rough)">
      <polygon points="47,288 797,168 797,248 47,368"/>
      <polygon points="47,768 797,648 797,748 47,888"/>
      <polygon points="47,1150 797,945 797,1200 47,1200"/>
    </g>
  </svg>

  <div class="portrait portrait--dorsey" role="img" aria-label="Posterized portrait of Lyle Dorsey"></div>
  <div class="portrait portrait--selvapathi" role="img" aria-label="Posterized portrait of Ravindra Selvapathi"></div>
  <div class="portrait portrait--falco" role="img" aria-label="Posterized portrait of Ned Falco"></div>
  <div class="portrait portrait--prisco" role="img" aria-label="Posterized portrait of Walt Prisco"></div>
  <div class="portrait portrait--pembrook" role="img" aria-label="Posterized portrait of Rufus Pembrook"></div>
  <div class="portrait portrait--quenby" role="img" aria-label="Posterized portrait of Harold Quenby"></div>

  <p class="quote quote--dorsey">
    <span>“What’s the one thing you can do, such</span>
    <span>that by doing it, everything else will be</span>
    <span>easier or unnecessary?”</span>
  </p>
  <p class="quote quote--selvapathi">
    <span>“If we can really understand the problem, the</span>
    <span>answer will come out of it, because the answer</span>
    <span>is not separate from the problem.”</span>
  </p>
  <p class="quote quote--falco">
    <span>“Success is nothing more than a few simple</span>
    <span>disciplines, practiced every day; while failure is</span>
    <span>simply a few errors in judgment, repeated every</span>
    <span>day. It is the accumulative weight of our disciplines</span>
    <span>and our judgments that leads us to either fortune or</span>
    <span>failure.”</span>
  </p>
  <p class="quote quote--prisco">
    <span>“I tackle every big new problem by asking two</span>
    <span>questions: Who has dealt with this problem well?</span>
    <span>And what can we learn from them?”</span>
  </p>
  <p class="quote quote--pembrook">
    <span>“Inaction breeds doubt and fear. Action breeds</span>
    <span>confidence and courage.”</span>
  </p>
  <p class="quote quote--quenby">
    <span>“What the pupil must learn, if he learns anything at all,</span>
    <span>is that the world will do most of the work for you,</span>
    <span>provided you cooperate with it by identifying how it</span>
    <span>really works and aligning with those realities. If we do</span>
    <span>not let the world teach us, it teaches us a lesson.”</span>
  </p>
</div>
</body>
</html>
```